Business Card Design

Copper Wing Bus Charters, name was derived from the Yellow Tail jack (fish). We are a school bus charter service that offers supplemental bus transportation to district schools for field trips, school sporting events, etc. We also offer bus service to recreation centers during summer time for field trips.
Our business incorporates the color sea or royal blue, school bus yellow and a dark or charcoal gray. Its a copy of the fish's natural color scheme.

I am looking for a logo with the color scheme listed. I am looking for something modern and professional.

Target Market(s)

School Administrators, City employees

Industry/Entity Type

Recreation

Contact Information for Business Card

Copper Wing Bus Charters LLC
Safe Reliable Affordable
Dermot Halvorsenby, Owner
P.O.BOX 28671
St. Petersburg, Fl 33733
555-314-9827
www.ridecopperwing.example
ridecopperwing@mailbox.example

Requirements
Should not have
• pictures of fish or buses

```html
<!DOCTYPE html>
<html lang="en">
<head>
<meta charset="utf-8">
<title>Copper Wing Bus Charters LLC – Business Card</title>
<link href="https://fonts.googleapis.com/css2?family=Exo+2:ital,wght@0,400;0,500;0,700;1,400&display=swap" rel="stylesheet">
<style>
  :root {
    --backdrop: #c6c7c9;
    --card-light: #ececec;
    --card-top: #e4e6e8;
    --brand-blue: #0eaeea;
    --ink-dark: #2f3133;
    --ink-white: #ffffff;
  }
  * { box-sizing: border-box; margin: 0; padding: 0; }
  html, body {
    width: 1200px; height: 949px; overflow: hidden;
    background: var(--backdrop);
    font-family: "Exo 2", Arial, sans-serif;
  }
  .sheet { position: relative; width: 1200px; height: 949px; }
  .card {
    position: absolute; left: 250px; width: 700px; height: 400px;
    border-radius: 24px; overflow: hidden;
  }
  .card--front { top: 54px; background: var(--card-light); }
  .card--back { top: 495px; background: var(--card-top); }

  .wordmark { position: absolute; color: var(--brand-blue); font-weight: 700; text-transform: uppercase; line-height: 1; }
  .wordmark__name { display: block; font-size: 50px; letter-spacing: 3px; }
  .wordmark__sub { display: block; font-size: 27px; letter-spacing: 5.5px; margin-top: 4px; }

  .card--front .wordmark { left: 0; right: 0; top: 130px; text-align: center; }
  .front-web {
    position: absolute; left: 196px; top: 262px;
    font-size: 15px; letter-spacing: 1.5px; color: var(--ink-dark); font-weight: 500;
  }

  .card--back .wordmark { left: 170px; top: 40px; }
  .band {
    position: absolute; left: 0; right: 0; top: 160px; bottom: 0;
    background: var(--brand-blue);
  }
  .holder { position: absolute; left: 56px; top: 178px; color: var(--ink-white); }
  .holder__name { font-size: 21px; letter-spacing: 2px; text-transform: uppercase; font-weight: 500; }
  .holder__role { font-size: 12px; letter-spacing: 1.5px; text-transform: uppercase; font-style: italic; margin-left: 26px; }

  .contact { position: absolute; display: flex; align-items: center; gap: 14px; color: var(--ink-white); font-size: 17px; letter-spacing: 1px; }
  .contact svg { width: 28px; height: 28px; flex: none; }
  .contact--phone { left: 52px; top: 230px; }
  .contact--mail { left: 52px; top: 282px; }
  .contact--address { left: 380px; top: 290px; line-height: 1.2; }
  .contact--web { left: 380px; top: 345px; }
</style>
</head>
<body>
<main class="sheet">
  <section class="card card--front" aria-label="Card front">
    <div class="wordmark">
      <span class="wordmark__name">Copper Wing</span>
      <span class="wordmark__sub">Bus Charters LLC</span>
    </div>
    <p class="front-web">www.urwebsite.com</p>
  </section>

  <section class="card card--back" aria-label="Card back">
    <div class="band"></div>
    <div class="wordmark">
      <span class="wordmark__name">Copper Wing</span>
      <span class="wordmark__sub">Bus Charters LLC</span>
    </div>
    <p class="holder"><span class="holder__name">Alden Marsh</span><span class="holder__role">Founder</span></p>

    <p class="contact contact--phone">
      <svg viewBox="0 0 28 28" fill="none" stroke="#fff" stroke-width="2"><circle cx="14" cy="14" r="12"/><path d="M10 8c-1.5 1-1.5 3 0 6s3.5 5 6 6c1.5.5 2.5 0 3-1l-2.5-2-1.5 1c-1.5-.8-3-2.6-3.5-4l1-1.2-1.5-3z" fill="#fff" stroke="none"/></svg>
      012 345 6789
    </p>
    <p class="contact contact--mail">
      <svg viewBox="0 0 28 28" fill="none" stroke="#fff" stroke-width="2"><circle cx="14" cy="14" r="12"/><rect x="8" y="10" width="12" height="8" fill="#fff" stroke="none"/><path d="M8 10l6 4 6-4" stroke="#0eaeea" stroke-width="1.3"/></svg>
      urname@email.com
    </p>
    <p class="contact contact--address">
      <svg viewBox="0 0 28 28" fill="none" stroke="#fff" stroke-width="2"><circle cx="14" cy="14" r="12"/><path d="M14 21s-5-5-5-8.5a5 5 0 0 1 10 0C19 16 14 21 14 21z"/><circle cx="14" cy="12.5" r="1.6" fill="#fff" stroke="none"/></svg>
      <span>041 9th floor Plaza<br>Harbor Road LKG</span>
    </p>
    <p class="contact contact--web">
      <svg viewBox="0 0 28 28" fill="none" stroke="#fff" stroke-width="2"><circle cx="14" cy="14" r="12"/><g stroke-width="1.4"><circle cx="14" cy="14" r="6.5"/><path d="M7.5 14h13M14 7.5v13M9 10.5h10M9 17.5h10"/></g></svg>
      www.urwebsite.com
    </p>
  </section>
</main>
</body>
</html>
```